Church needs a street sign design

We're a small church located in Silicon Valley, California. Our website is https://www.vgtmarlowfield.org/ and our address is 4817 Ferrow Ave, San Jose, California, 95873. You can look up our location on Google Maps to see the sign from Street View. I have uploaded an image of the street sign as well. The marquee, the top section of the sign, and the separating line between them both will be removed. We're seeking a design for a new backlit acrylic insert that will go on the front of the light box and the back of the lightbox. The acrylic sign will fill the entire external frame. In the future, we may build a decorative wood frame around the structural legs, as visualized in one of the uploaded files. The church's brand colors are: #003366 (dark blue), #ff6600 (vibrant orange), #228b22 (forest green). I have also uploaded the church's logo assets. Our primary font is Montserrat and the secondary is Poppins. You can deviate from these colors/fonts if the sign is still coherent with the rest of our branding. Our branding values are mission, truth, passion, and community (please do not put those words on the sign! They are just intended to guide the look of the design). The sign dimensions are 96" by 47.5". Keep in mind that the sign will be backlit on a busy street side. It will also be positioned next to an old-looking church building. We do NOT want a sign that looks traditional, old, or antiquated. Instead, we want a modern-looking sign that pairs well with our old building while helping it look more modern too. We would also like the web address clearly visible on the sign: vgtmarlowfield.org. If you have any questions, just let me know!

```html
<!DOCTYPE html>
<html lang="en">
<head>
<meta charset="utf-8">
<title>Marlowfield Community Church – Street Sign</title>
<link href="https://fonts.googleapis.com/css2?family=Montserrat:wght@600;700;800&family=Sacramento&display=swap" rel="stylesheet">
<style>
  :root {
    --navy: #131f4b;
    --navy-deep: #0d1738;
    --sky: #3fa3f5;
    --orange: #ff6a00;
    --white: #ffffff;
    --page: #ffffff;
  }
  html, body {
    margin: 0;
    padding: 0;
    width: 875px;
    height: 1200px;
    overflow: hidden;
    background: var(--page);
  }
  .sign {
    position: absolute;
    left: 37px;
    top: 402px;
    width: 800px;
    height: 396px;
    background: var(--navy);
    box-shadow: 8px 10px 12px rgba(0, 0, 0, 0.45);
    overflow: hidden;
  }
  .sign-art {
    position: absolute;
    inset: 0;
    width: 800px;
    height: 396px;
  }
  .headline {
    position: absolute;
    left: 47px;
    top: 44px;
    margin: 0;
    font-family: "Montserrat", sans-serif;
    font-weight: 800;
    font-size: 57px;
    line-height: 50px;
    letter-spacing: -1px;
    color: var(--white);
  }
  .subhead {
    position: absolute;
    left: 48px;
    top: 158px;
    margin: 0;
    font-family: "Montserrat", sans-serif;
    font-weight: 800;
    font-size: 28px;
    line-height: 30px;
    color: var(--sky);
  }
  .tagline {
    position: absolute;
    left: 46px;
    top: 232px;
    margin: 0;
    font-family: "Sacramento", cursive;
    font-size: 35px;
    line-height: 40px;
    color: var(--white);
  }
  .web-band {
    position: absolute;
    left: 0;
    top: 310px;
    width: 354px;
    height: 45px;
  }
  .web-address {
    position: absolute;
    left: 46px;
    top: 310px;
    height: 45px;
    margin: 0;
    font-family: "Montserrat", sans-serif;
    font-weight: 800;
    font-size: 23px;
    line-height: 45px;
    letter-spacing: 0.6px;
    color: var(--white);
    text-shadow: 1px 2px 2px rgba(0, 0, 0, 0.35);
    text-decoration: none;
  }
  .church-mark {
    position: absolute;
    left: 620px;
    top: 312px;
    display: flex;
    align-items: center;
    gap: 9px;
  }
  .church-mark-square {
    width: 26px;
    height: 26px;
    border: 2px solid var(--white);
    box-sizing: border-box;
  }
  .church-name {
    margin: 0;
    font-family: "Montserrat", sans-serif;
    font-weight: 600;
    color: var(--white);
  }
  .church-name-main {
    display: block;
    font-size: 17px;
    line-height: 18px;
    letter-spacing: 0.3px;
  }
  .church-name-sub {
    display: block;
    font-size: 7.6px;
    line-height: 10px;
    letter-spacing: 0.4px;
  }
</style>
</head>
<body>
  <main class="sign" aria-label="Church street sign">
    <svg class="sign-art" viewBox="0 0 1379 682" preserveAspectRatio="none">
      <defs>
        <linearGradient id="sky-fill" x1="0" y1="0" x2="0" y2="1">
          <stop offset="0" stop-color="#3aa4f6"/>
          <stop offset="0.6" stop-color="#1f5cbc"/>
          <stop offset="1" stop-color="#131f4b"/>
        </linearGradient>
        <linearGradient id="photo-fill" x1="0" y1="0" x2="0" y2="1">
          <stop offset="0" stop-color="#3a2a2c"/>
          <stop offset="0.45" stop-color="#b8621f"/>
          <stop offset="0.7" stop-color="#6a3a1c"/>
          <stop offset="1" stop-color="#0a0a0a"/>
        </linearGradient>
        <linearGradient id="right-glow" x1="0" y1="0" x2="1" y2="0">
          <stop offset="0" stop-color="#1e3f9a"/>
          <stop offset="0.5" stop-color="#16296b"/>
          <stop offset="1" stop-color="#131f4b"/>
        </linearGradient>
        <linearGradient id="accent-fill" x1="0" y1="0" x2="0" y2="1">
          <stop offset="0" stop-color="#2f7fe0"/>
          <stop offset="1" stop-color="#5fbcff"/>
        </linearGradient>
      </defs>

      <polygon class="sky-panel" role="img" aria-label="Photo of blue sky with clouds" points="615,0 845,0 620,540 520,560" fill="url(#sky-fill)" opacity="0.9"/>

      <polygon class="side-glow" points="1290,0 1379,0 1379,682 950,682" fill="url(#right-glow)"/>

      <polygon class="cross-photo" role="img" aria-label="Photo of a cross on a hill at sunset" points="845,0 1290,0 950,682 505,682" fill="url(#photo-fill)"/>

      <polygon class="accent-triangle" points="1120,342 1185,472 1055,472" fill="url(#accent-fill)"/>
    </svg>

    <h1 class="headline">MAKING<br>DISCIPLES</h1>
    <p class="subhead">&amp; HELPING THE<br>HELPLESS</p>
    <p class="tagline">For the Glory of Christ</p>

    <svg class="web-band" viewBox="0 0 354 45" preserveAspectRatio="none" aria-hidden="true">
      <polygon points="0,0 354,0 332,45 0,45" fill="var(--orange)"/>
    </svg>
    <a class="web-address" href="https://www.vgtmarlowfield.org/">vgtmarlowfield.org</a>

    <div class="church-mark">
      <span class="church-mark-square" aria-hidden="true"></span>
      <p class="church-name">
        <span class="church-name-main">MARLOWFIELD</span>
        <span class="church-name-sub">COMMUNITY CHURCH</span>
      </p>
    </div>
  </main>
</body>
</html>
```